Design a modern, classy & professional business card for an online real estate agency, specializing in medium-luxury properties in Thailand and later in Singapore and UK.

Possible design ideas so far: (not essential)

- curved corner(s) to the card, white on front & turquoise on back or visa versa.

- front of card - clear and simple, company name in metallic grey/monochrome, logo graphic & company name on front in spot UV or embossed/debossed effect.

- back of card - large, close-cropped, 'ghost' patterns of the C-shaped curves of logo, or company name repeated on back of card in spot UV.

Target Market(s)

- young to middle-aged professionals mainly (but ideally should design should suit all)

- UK, US,EU,AUS & ASIAN mainly (but ideally should design should suit all countries)

Industry/Entity Type

Real Estate

Requirements
Must have
• THEME:
- Luxurious & Modern
- Clean & striking
- Unique & creative

INFO:
- Logo & company name on front
- Contact details on back:

Tobias Hennlund
Managing Director

www.velmontestates.asia
www.velmontestates.co.uk

Tel: 083-274-6159
email: tobias@velmontestates.asia

(contact details can be displayed in any order as suites design.)

Nice to have
• - curved corner(s) to the card, white on front & turquoise on back or visa versa.

Should not have
• - No generic images of properties, palm trees/coconut trees etc.

- No other other bold colors, except for main turquoise, grey, metallic white & black theme.

- No obvious business card templates

```html
<!DOCTYPE html>
<html lang="en">
<head>
<meta charset="utf-8">
<title>Velmont Estates – Business Card</title>
<link rel="stylesheet" href="https://fonts.googleapis.com/css2?family=Aldrich&display=swap">
<style>
  :root {
    --turquoise: #1fc2c0;
    --ink: #2a2a2a;
    --grey: #7d7f80;
    --rule: #9a9c9d;
    --paper: #ffffff;
    --backdrop: #e9eaeb;
  }
  html, body {
    margin: 0;
    width: 1200px;
    height: 1057px;
    overflow: hidden;
    background: var(--backdrop);
    font-family: "Aldrich", sans-serif;
  }
  .card {
    position: absolute;
    left: 310px;
    top: 63px;
    width: 580px;
    height: 930px;
    background: var(--paper);
    box-shadow: 0 10px 30px rgba(0,0,0,0.12);
  }
  .brand {
    position: absolute;
    left: 150px;
    top: 90px;
    display: flex;
    flex-direction: column;
    align-items: flex-start;
  }
  .brand-square {
    width: 84px;
    height: 84px;
    background: var(--turquoise);
  }
  .brand-name {
    margin-top: 18px;
    font-size: 40px;
    color: var(--grey);
    letter-spacing: 1px;
    line-height: 1;
  }
  .contact-panel {
    position: absolute;
    left: 50px;
    right: 44px;
    top: 330px;
    bottom: 50px;
    border: 2px solid var(--rule);
    border-radius: 40px;
    box-sizing: border-box;
  }
  .person {
    position: absolute;
    left: 30px;
    top: 30px;
  }
  .person-name {
    font-size: 38px;
    color: var(--turquoise);
    letter-spacing: 2px;
    line-height: 1;
  }
  .person-title {
    margin-top: 10px;
    font-size: 15px;
    color: var(--turquoise);
    letter-spacing: 2px;
  }
  .contact-list {
    position: absolute;
    left: 30px;
    right: 30px;
    top: 130px;
    margin: 0;
    padding: 0;
    list-style: none;
  }
  .contact-row {
    display: flex;
    align-items: center;
    justify-content: space-between;
    height: 74px;
    border-bottom: 1.5px solid var(--rule);
  }
  .contact-row:last-child {
    height: 96px;
    border-bottom: none;
  }
  .contact-key {
    flex: none;
    width: 26px;
    height: 26px;
    border: 1.5px solid var(--rule);
    box-sizing: border-box;
    display: flex;
    align-items: center;
    justify-content: center;
    font-size: 12px;
    color: var(--turquoise);
  }
  .contact-value {
    font-size: 19px;
    color: var(--ink);
    letter-spacing: 1px;
    text-align: right;
    line-height: 1.4;
  }
</style>
</head>
<body>
  <main class="card">
    <div class="brand">
      <div class="brand-square"></div>
      <div class="brand-name">Velmont Estates</div>
    </div>

    <section class="contact-panel">
      <div class="person">
        <div class="person-name">TOBIAS HENNLUND</div>
        <div class="person-title">MANAGING DIRECTOR</div>
      </div>
      <ul class="contact-list">
        <li class="contact-row"><span class="contact-key">P</span><span class="contact-value">083-274-6159</span></li>
        <li class="contact-row"><span class="contact-key">E</span><span class="contact-value">tobias@velmontestates.asia</span></li>
        <li class="contact-row"><span class="contact-key">W</span><span class="contact-value">www.velmontestates.asia</span></li>
        <li class="contact-row"><span class="contact-key">W</span><span class="contact-value">www.velmontestates.co.uk</span></li>
        <li class="contact-row"><span class="contact-key">A</span><span class="contact-value">27 Lumen Park Road,<br>4th Floor Suite B</span></li>
      </ul>
    </section>
  </main>
</body>
</html>
```